I need a flyer made , the flyer can be one page or two pages or three pages . I will be posting this on Instagram and social media platforms. I am a luxury home builder , I am looking to hire a construction project manager . Below are some examples and ideas what can be on the flyer

We’re looking for a construction project manager who’s passionate about building luxury homes at the highest standards
We’re hiring construction project manager
* Experience 5+ years in residential project management with a strong portfolio of completed homes.
* location : Bergen County NJ
* excellent leadership skills, leads teams with confidence and clarity
* communicates seamlessly with architects , engineers, designers and clients
*knows how to manage budgets and timelines without compromising quality
*solves problems with a positive solution first mindset
* pays attention to every detail because in luxury the small things are the big things

Apply now , link in bio or DM to connect.

My logo is attached, my web site www.velstridebuilders.com
My style is modern but still warm and inviting. I like a clean classy look .

Please don’t add any images of chairs or people to the flyer , I do not want people on my flyer. Do not add standard images of offices and houses , we are luxury builders , we build homes over 2 million dollars. Keep a classy , simple modern look . High end .

You can add a white hard hat with my logo on it for a image , this is a suggestion does not have to be on my flyer ,

```html
<!DOCTYPE html>
<html lang="en">
<head>
<meta charset="utf-8">
<title>Velstride Builders – We're Hiring</title>
<link href="https://fonts.googleapis.com/css2?family=Poppins:wght@200;300;400;600;700&display=swap" rel="stylesheet">
<style>
  :root {
    --stage: #cdd2d9;
    --ink: #0b0b0c;
    --paper: #eef0ef;
    --haze-light: #f3f4f3;
    --haze-mid: #dfe3e1;
    --haze-green: #c9d2c9;
    --photo-sky: #6f7f88;
    --photo-pool: #2f8fa6;
    --photo-warm: #b98b52;
    --photo-dark: #27332e;
    --band: #c8ccd3;
    --rule: #9a9da3;
    --bullet: #8d9096;
    --white: #ffffff;
  }
  * { margin: 0; padding: 0; box-sizing: border-box; }
  html, body {
    width: 1200px; height: 692px; overflow: hidden;
    background: var(--stage);
    font-family: "Poppins", sans-serif;
    color: var(--ink);
  }
  .post {
    position: absolute; top: 116px;
    width: 465px; height: 465px; overflow: hidden;
    background: var(--paper);
  }
  .post--cover { left: 119px; }
  .post--details { left: 596px; }
  .post svg.shapes { position: absolute; inset: 0; width: 465px; height: 465px; }

  .brand {
    position: absolute; top: 44px;
    font-family: "Poppins", sans-serif; font-weight: 300;
    font-size: 21px; letter-spacing: 3px; line-height: 1;
    color: var(--ink); white-space: nowrap;
  }
  .post--cover .brand { left: 19px; }
  .post--details .brand { right: 16px; }

  .cover-title { position: absolute; left: 118px; top: 102px; }
  .cover-title__light {
    display: block; font-weight: 200; font-size: 72px; line-height: 72px;
    letter-spacing: -3px; padding-left: 30px;
  }
  .cover-title__bold {
    display: block; font-weight: 700; font-size: 69px; line-height: 62px;
    letter-spacing: -1px;
  }

  .site {
    position: absolute; top: 425px;
    font-size: 8px; font-weight: 300; color: var(--white); letter-spacing: 0.1px;
  }
  .post--cover .site { left: 18px; }
  .post--details .site { right: 16px; }

  .intro {
    position: absolute; right: 16px; top: 106px; width: 240px;
    text-align: right; font-weight: 700; font-size: 12.4px; line-height: 14px;
  }
  .role { position: absolute; right: 16px; top: 196px; text-align: right; }
  .role__kicker { display: block; font-weight: 200; font-size: 28px; line-height: 24px; letter-spacing: -1px; }
  .role__title { display: block; font-weight: 700; font-size: 29.5px; line-height: 24px; letter-spacing: -0.3px; }
  .role__rule { position: absolute; left: 196px; top: 274px; width: 253px; height: 3px; background: var(--rule); }

  .requirements { position: absolute; left: 47px; top: 286px; list-style: none; }
  .requirements li {
    position: relative; padding-left: 10px;
    font-size: 8.1px; font-weight: 300; line-height: 17.2px; white-space: nowrap;
  }
  .requirements li::before {
    content: ""; position: absolute; left: 0; top: 7px;
    width: 4px; height: 4px; background: var(--bullet);
  }

  .cta { position: absolute; left: 18px; top: 420px; line-height: 11px; font-size: 10.6px; }
  .cta__lead { display: block; font-weight: 700; }
  .cta__action { display: block; font-weight: 300; }
</style>
</head>
<body>

<section class="post post--cover">
  <svg class="shapes" viewBox="0 0 465 465" aria-hidden="false">
    <defs>
      <linearGradient id="coverHaze" x1="0" y1="0" x2="0.4" y2="1">
        <stop offset="0" stop-color="var(--haze-light)"/>
        <stop offset="0.55" stop-color="var(--haze-mid)"/>
        <stop offset="1" stop-color="var(--haze-green)"/>
      </linearGradient>
      <linearGradient id="coverPhoto" x1="0" y1="0" x2="1" y2="1">
        <stop offset="0" stop-color="var(--photo-sky)"/>
        <stop offset="0.4" stop-color="var(--photo-warm)"/>
        <stop offset="0.65" stop-color="var(--photo-pool)"/>
        <stop offset="1" stop-color="var(--photo-dark)"/>
      </linearGradient>
    </defs>
    <rect width="465" height="465" fill="url(#coverHaze)" role="img" aria-label="Faded aerial view of a hillside luxury home with a line drawing of its facade"/>
    <polygon points="465,111 465,357 335,465 111,465" fill="url(#coverPhoto)" role="img" aria-label="Aerial photo of a modern glass villa with infinity pool at dusk"/>
    <rect x="356" y="417" width="109" height="30" fill="var(--band)" opacity="0.85"/>
    <polygon points="0,417 152,417 122,447 0,447" fill="var(--ink)"/>
  </svg>

  <div class="brand">VELSTRIDE BUILDERS</div>

  <h1 class="cover-title">
    <span class="cover-title__light">WE’RE</span>
    <span class="cover-title__bold">HIRING</span>
  </h1>

  <p class="site">www.velstridebuilders.com</p>
</section>

<section class="post post--details">
  <svg class="shapes" viewBox="0 0 465 465">
    <defs>
      <linearGradient id="detailHaze" x1="0" y1="0" x2="0.3" y2="1">
        <stop offset="0" stop-color="var(--haze-light)"/>
        <stop offset="0.6" stop-color="var(--haze-mid)"/>
        <stop offset="1" stop-color="var(--haze-light)"/>
      </linearGradient>
      <linearGradient id="detailPhoto" x1="0" y1="0" x2="0.6" y2="1">
        <stop offset="0" stop-color="var(--photo-dark)"/>
        <stop offset="0.45" stop-color="var(--photo-warm)"/>
        <stop offset="0.8" stop-color="var(--photo-sky)"/>
        <stop offset="1" stop-color="var(--photo-pool)"/>
      </linearGradient>
    </defs>
    <rect width="465" height="465" fill="url(#detailHaze)" role="img" aria-label="Faded close view of a luxury home terrace"/>
    <polygon points="103,0 323,0 0,322 0,101" fill="url(#detailPhoto)" role="img" aria-label="Photo of glass-walled upper floors of a modern villa set among trees"/>
    <rect x="0" y="417" width="345" height="30" fill="var(--band)"/>
    <polygon points="338,417 465,417 465,447 311,447" fill="var(--ink)"/>
  </svg>

  <div class="brand">VELSTRIDE BUILDERS</div>

  <p class="intro">We’re looking for a construction project manager who’s passionate about building luxury homes at the highest standards</p>

  <h2 class="role">
    <span class="role__kicker">WE’RE HIRING</span>
    <span class="role__title">CONSTRUCTION</span>
    <span class="role__title">PROJECT MANAGER</span>
  </h2>
  <div class="role__rule"></div>

  <ul class="requirements">
    <li>Experience 5+ years in residential project management with a strong portfolio of completed homes</li>
    <li>Location : Bergen County NJ</li>
    <li>Excellent leadership skills, leads teams with confidence and clarity</li>
    <li>Communicates seamlessly with architects, engineers, designers and clients</li>
    <li>Knows how to manage budgets and timelines without compromising quality</li>
    <li>Solves problems with a positive solution first mindset</li>
    <li>Pays attention to every detail because in luxury the small things are the big things</li>
  </ul>

  <p class="cta">
    <span class="cta__lead">APPLY NOW,</span>
    <span class="cta__action">LINK IN BIO OR DM TO CONNECT</span>
  </p>

  <p class="site">www.velstridebuilders.com</p>
</section>

</body>
</html>
```